RW Framewell Inc Business cards

We need business cards using our existing logo but slightly modified. Right now the logo says RW Loadbearing Masonry. We want to keep the RW part of the design, but replace the Structural Concrete portion with "FRAMEWELL". Please see the attached file.
Ideally this would be a blank template so we can add Different Names, titles, and phone numbers later.
On the one side we want only the logo and on the other side the detail. I'm attaching an example for you to see.
Please reach out with any other questions. Our address and other details will be given out once we find a design we like.

Target Market(s)

Construction Industry

```html
<!DOCTYPE html>
<html lang="en">
<head>
<meta charset="utf-8">
<title>RW Framewell Inc – Business Cards</title>
<link rel="stylesheet" href="https://fonts.googleapis.com/css2?family=Archivo+Black&family=Roboto:wght@400&display=swap">
<style>
  :root {
    --backdrop: #b8b8b8;
    --brand-blue: #1c75bc;
    --card-white: #ffffff;
    --text-white: #ffffff;
  }
  * { margin: 0; padding: 0; box-sizing: border-box; }
  html, body {
    width: 1200px;
    height: 801px;
    overflow: hidden;
    background: var(--backdrop);
  }
  .sheet {
    position: relative;
    width: 1200px;
    height: 801px;
  }
  .card {
    position: absolute;
    top: 274px;
    width: 443px;
    height: 263px;
    background: var(--card-white);
    overflow: hidden;
  }
  .card--details { left: 153px; }
  .card--brand { left: 625px; }

  /* Details side */
  .details-panel {
    position: absolute;
    left: 0;
    top: 0;
    width: 214px;
    height: 100%;
    background: var(--brand-blue);
    color: var(--text-white);
    padding: 87px 0 0 21px;
  }
  .person-name {
    font-family: "Archivo Black", sans-serif;
    font-size: 15px;
    letter-spacing: 0.2px;
    line-height: 1;
  }
  .person-title {
    font-family: "Roboto", sans-serif;
    font-size: 13px;
    line-height: 1.2;
    margin-top: 2px;
  }
  .contact-list {
    list-style: none;
    margin-top: 18px;
    font-family: "Roboto", sans-serif;
    font-size: 13px;
    line-height: 16.5px;
  }
  .contact-list li {
    display: flex;
    align-items: center;
    gap: 4px;
    white-space: nowrap;
  }
  .contact-icon {
    width: 13px;
    height: 13px;
    flex: none;
  }
  .details-mark {
    position: absolute;
    left: 220px;
    top: 0;
    width: 223px;
    height: 100%;
    display: flex;
    align-items: center;
    justify-content: center;
  }
  .details-mark__name {
    font-family: "Archivo Black", sans-serif;
    font-size: 120px;
    line-height: 1;
    color: var(--brand-blue);
    letter-spacing: -2px;
  }

  /* Brand side */
  .brand-lockup {
    position: absolute;
    inset: 0;
    display: flex;
    flex-direction: column;
    align-items: center;
    justify-content: center;
    color: var(--brand-blue);
    font-family: "Archivo Black", sans-serif;
    line-height: 1;
  }
  .brand-lockup__initials {
    font-size: 108px;
    letter-spacing: -2px;
  }
  .brand-lockup__word {
    font-size: 29px;
    letter-spacing: 1px;
    margin-top: 6px;
  }
</style>
</head>
<body>
<main class="sheet">

  <section class="card card--details" aria-label="Business card, contact side">
    <div class="details-panel">
      <h1 class="person-name">DANIEL PORTER</h1>
      <p class="person-title">Managing Director</p>
      <ul class="contact-list">
        <li>
          <svg class="contact-icon" viewBox="0 0 24 24" aria-hidden="true">
            <path fill="none" stroke="currentColor" stroke-width="2.2" stroke-linejoin="round"
              d="M5 3h4l2 5-2.5 1.5a11 11 0 0 0 6 6L16 13l5 2v4a2 2 0 0 1-2 2A16 16 0 0 1 3 5a2 2 0 0 1 2-2z"/>
          </svg>
          <span>044-987 654 321</span>
        </li>
        <li>
          <svg class="contact-icon" viewBox="0 0 24 24" aria-hidden="true">
            <rect x="2" y="5" width="20" height="14" fill="currentColor"/>
            <path d="M2 5l10 8 10-8" fill="none" stroke="#1c75bc" stroke-width="1.6"/>
          </svg>
          <span>info@rwframewell.com</span>
        </li>
        <li>
          <svg class="contact-icon" viewBox="0 0 24 24" aria-hidden="true">
            <g fill="none" stroke="currentColor" stroke-width="1.8">
              <circle cx="12" cy="12" r="10"/>
              <ellipse cx="12" cy="12" rx="4.5" ry="10"/>
              <path d="M2 12h20M4 7h16M4 17h16"/>
            </g>
          </svg>
          <span>www.rwframewell.com</span>
        </li>
      </ul>
    </div>
    <div class="details-mark">
      <span class="details-mark__name">RW</span>
    </div>
  </section>

  <section class="card card--brand" aria-label="Business card, logo side">
    <div class="brand-lockup">
      <span class="brand-lockup__initials">RW</span>
      <span class="brand-lockup__word">FRAMEWELL</span>
    </div>
  </section>

</main>
</body>
</html>
```